Stretch on the Green with Mira

I want to advertise my Stretch on the Green classes for Summer. Classes are outside at the lovely local park. Tolmore field. 12 Rawhiti St. Sandringham.
Classes are for beginners to advance levels.
Classes start Monday, October 17th.
Monday 6pm Beginners
Tuesday 6pm Intermediate
Thursday 6pm Intermediate/Advance
Saturday 9am All fitness levels
My Pilates classes are specially designed to help improve strength and flexibility but as well will also improve posture, reduce stress and develop control and endurance in the entire body.
Booking essential. Limited numbers so I can make sure the correct technique is always being followed.
For more info or to book contact details:
Mira 027385116
mira@stretchwithmira.net
www.stretchwithmira.net
$15 Per Session

Target Market(s)

Males and Females ages 35plus.

Industry/Entity Type

Fitness

Font styles to use
Sans Serif

Requirements
Must have
• My logo. Contact details. A Park that looks lovely to exercise at.
Nice to have
• Summer looking. Trees - inspiration to be exercising outside

```html
<!DOCTYPE html>
<html lang="en">
<head>
<meta charset="utf-8">
<title>Stretch on the Green – Classes for Summer</title>
<link href="https://fonts.googleapis.com/css2?family=Playfair+Display:wght@700;800&family=Dancing+Script:wght@600;700&family=Poppins:wght@400;500;600;700&display=swap" rel="stylesheet">
<style>
  :root{
    --green-dark:#1d5a47;
    --green:#2f7a52;
    --green-light:#7faa4a;
    --pink:#e4a0a6;
    --cream:#f7f1e8;
    --card:#f3ece2;
    --ink:#2b2b2b;
    --page:#eeeeec;
    --white:#ffffff;
  }
  *{box-sizing:border-box;margin:0;padding:0}
  html,body{width:1200px;height:2244px;overflow:hidden;background:var(--page)}
  body{font-family:"Poppins",Arial,sans-serif;color:var(--ink);position:relative}
  .flyer{position:absolute;left:32px;top:462px;width:1136px;height:1320px;background:var(--white);overflow:hidden;box-shadow:0 6px 24px rgba(0,0,0,.12)}
  .abs{position:absolute}

  .hero-photo{left:300px;top:0;width:836px;height:310px;
    background:linear-gradient(180deg,#bcd6e6 0%,#a8c98a 45%,#5f8f3c 75%,#7a9a55 100%)}
  .hero-fade{left:0;top:0;width:760px;height:330px;
    background:linear-gradient(90deg,#fff 0%,#fff 45%,rgba(255,255,255,.85) 62%,rgba(255,255,255,0) 100%)}
  .hero-bottom{left:0;top:270px;width:1136px;height:60px;background:linear-gradient(180deg,rgba(255,255,255,0),#fff)}

  .brand{left:40px;top:22px;display:flex;align-items:center;gap:12px;
    font-family:"Poppins",sans-serif;font-weight:600;font-size:17px;letter-spacing:1px;color:var(--green-dark);text-transform:uppercase;width:260px;line-height:1.25}
  .brand-dot{width:34px;height:34px;border-radius:50%;background:var(--green-dark);flex:none}

  .title{left:40px;top:120px;font-family:"Playfair Display",serif;font-weight:800;color:var(--green-dark);text-transform:uppercase;line-height:.98}
  .title .l1{font-size:96px;display:block}
  .title .l2{font-size:58px;display:block;letter-spacing:1px}
  .subtitle{left:44px;top:262px;font-family:"Dancing Script",cursive;font-weight:700;font-size:60px;color:var(--green)}

  .round-photo{left:730px;top:225px;width:270px;height:270px;border-radius:50%;
    border:10px solid var(--white);box-shadow:0 0 0 7px var(--green-dark);
    background:radial-gradient(circle at 40% 35%,#cfe3ef 0%,#a9c98d 55%,#5e8c3b 100%)}

  .intro{left:40px;top:392px;font-size:27px;font-weight:500}
  .location{left:40px;top:440px;width:670px;height:58px;border:3px solid var(--green-dark);border-left:14px solid var(--green-dark);
    display:flex;align-items:center;padding-left:18px;font-weight:700;font-size:21px;color:var(--green-dark);text-transform:uppercase;letter-spacing:.3px;white-space:nowrap}

  .section-head{left:40px;width:1056px;display:flex;align-items:center;gap:18px;font-weight:700;text-transform:uppercase;color:var(--green-dark);font-size:27px}
  .section-head::before,.section-head::after{content:"";flex:1;height:3px;background:var(--pink)}
  .section-head .pink{color:#c9606c}
  .levels-head{top:530px}
  .start-head{top:935px;font-size:30px}

  .cards{left:40px;top:590px;width:1056px;display:flex;gap:28px}
  .card{flex:1;background:var(--card);height:300px;position:relative;padding:14px}
  .card-photo{width:100%;height:150px;border:5px solid var(--green-dark);
    background:linear-gradient(180deg,#c8dfe9,#9fc27c 60%,#6f9448)}
  .card-name{margin-top:14px;text-align:center;font-weight:700;font-size:20px;text-transform:uppercase;color:var(--green-dark);line-height:1.15;height:50px;display:flex;align-items:center;justify-content:center}
  .card-time{position:absolute;left:14px;right:14px;bottom:14px;display:flex;justify-content:space-between;align-items:center;font-size:20px;font-weight:500}
  .card-time b{background:var(--green-dark);color:var(--white);padding:3px 10px;font-weight:600}

  .about{left:40px;top:990px;width:1056px;font-size:22px;line-height:1.5}

  .booking-tab{left:40px;top:1085px;background:var(--green-dark);color:var(--white);font-weight:700;font-size:22px;text-transform:uppercase;padding:6px 22px}
  .booking-box{left:40px;top:1122px;width:790px;border:3px solid var(--green-dark);padding:10px 20px;font-size:21px;line-height:1.4}

  .price{left:880px;top:1048px;width:180px;height:180px}
  .price-text{left:880px;top:1048px;width:180px;height:180px;display:flex;flex-direction:column;align-items:center;justify-content:center;color:var(--white)}
  .price-text .amount{font-weight:700;font-size:58px;line-height:1}
  .price-text .per{font-family:"Dancing Script",cursive;font-size:26px;font-weight:700}

  .footer{left:0;top:1235px;width:1136px;height:85px;background:var(--cream)}
  .footer-cta{left:0;top:1235px;width:440px;height:85px;background:var(--green-dark);color:var(--white);font-weight:600;font-size:24px;line-height:1.2;padding:12px 30px}
  .contact{display:flex;align-items:center;gap:10px;font-size:21px;font-weight:500;white-space:nowrap}
  .contact svg{flex:none}
  .phone{left:480px;top:1262px}
  .email{left:790px;top:1245px}
  .web{left:790px;top:1283px}
</style>
</head>
<body>
<main class="flyer">
  <div class="abs hero-photo" role="img" aria-label="Photo of a group doing stretches on mats under summer trees in a park"></div>
  <div class="abs hero-fade"></div>
  <div class="abs hero-bottom"></div>

  <div class="abs brand"><span class="brand-dot"></span>Stretch on the Green with Mira</div>

  <h1 class="abs title"><span class="l1">Stretch</span><span class="l2">On the Green</span></h1>
  <p class="abs subtitle">Classes for Summer</p>

  <div class="abs round-photo" role="img" aria-label="Photo of an instructor stretching on a mat on the grass"></div>

  <p class="abs intro">Classes are outside at the lovely local park</p>
  <p class="abs location">Tolmore Field (12 Rawhiti St, Sandringham)</p>

  <h2 class="abs section-head levels-head"><span>Classes are for <span class="pink">beginners to advance levels</span></span></h2>

  <section class="abs cards">
    <div class="card">
      <div class="card-photo" role="img" aria-label="Photo of a beginner stretch pose outdoors"></div>
      <p class="card-name">Beginners</p>
      <p class="card-time">Monday <b>6pm</b></p>
    </div>
    <div class="card">
      <div class="card-photo" role="img" aria-label="Photo of an intermediate lunge pose outdoors"></div>
      <p class="card-name">Intermediate</p>
      <p class="card-time">Tuesday <b>6pm</b></p>
    </div>
    <div class="card">
      <div class="card-photo" role="img" aria-label="Photo of an advanced balance pose outdoors"></div>
      <p class="card-name">Intermediate<br>/Advance</p>
      <p class="card-time">Thursday <b>6pm</b></p>
    </div>
    <div class="card">
      <div class="card-photo" role="img" aria-label="Photo of a seated mat stretch outdoors"></div>
      <p class="card-name">All fitness<br>levels</p>
      <p class="card-time">Saturday <b>9am</b></p>
    </div>
  </section>

  <h2 class="abs section-head start-head"><span>Classes start Monday, October 17th</span></h2>

  <p class="abs about">My Pilates classes are specially designed to help improve strength and flexibility but as well will also improve posture, reduce stress and develop control and endurance in the entire body.</p>

  <p class="abs booking-tab">Booking essential</p>
  <p class="abs booking-box">Limited numbers so I can make sure the correct technique is always being followed.</p>

  <svg class="abs price" viewBox="0 0 180 180" aria-hidden="true">
    <g fill="#1d5a47" transform="translate(90 90)">
      <rect x="-70" y="-70" width="140" height="140"/>
      <rect x="-70" y="-70" width="140" height="140" transform="rotate(30)"/>
      <rect x="-70" y="-70" width="140" height="140" transform="rotate(60)"/>
    </g>
    <circle cx="90" cy="90" r="72" fill="none" stroke="#fff" stroke-width="2" stroke-dasharray="4 4"/>
  </svg>
  <div class="abs price-text"><span class="amount">$15</span><span class="per">Per Session</span></div>

  <footer>
    <div class="abs footer"></div>
    <p class="abs footer-cta">For more info or to book<br>contact details</p>
    <p class="abs contact phone">
      <svg width="34" height="34" viewBox="0 0 24 24" aria-hidden="true"><circle cx="12" cy="12" r="12" fill="#1d5a47"/><path d="M8.2 6.5l2 2-1.2 1.6c.7 1.6 2 2.9 3.6 3.6l1.6-1.2 2 2-1.3 1.8c-4.2-.4-7.9-4.1-8.3-8.3z" fill="#fff"/></svg>
      027385116 (Mira)
    </p>
    <p class="abs contact email">
      <svg width="30" height="30" viewBox="0 0 24 24" aria-hidden="true"><circle cx="12" cy="12" r="12" fill="#1d5a47"/><rect x="6" y="8" width="12" height="8" fill="none" stroke="#fff" stroke-width="1.4"/><path d="M6 8l6 5 6-5" fill="none" stroke="#fff" stroke-width="1.4"/></svg>
      mira@stretchwithmira.net
    </p>
    <p class="abs contact web">
      <svg width="30" height="30" viewBox="0 0 24 24" aria-hidden="true"><circle cx="12" cy="12" r="12" fill="#1d5a47"/><circle cx="12" cy="12" r="6" fill="none" stroke="#fff" stroke-width="1.4"/><path d="M6 12h12M12 6c-2.5 3-2.5 9 0 12M12 6c2.5 3 2.5 9 0 12" fill="none" stroke="#fff" stroke-width="1.2"/></svg>
      www.stretchwithmira.net
    </p>
  </footer>
</main>
</body>
</html>
```